Stage Design Company Business Card

We are looking to step up up our business card design for our team.

We are a Full service Design and Consultation company for Stage and TV with an emphasis in Theatrical Lighting.

We like our materials to be clean and modern with solid colors free of patterns and gradients. Our brand consists of 4 primary colors Purple, Black, Grey, and White. Provided is our Word Mark as well as our Symbol Logo.

We would like our cards to leave an impression beyond the information, show our attention to design and detail, and make our marks an easily recognized feature (together or apart) for our clients.

We need a warm approachable comfortable feel for some clients, and a professional flair for the board member type clients.

Attached are our brand elements, and our existing cards to give a sense of our style and a glipse at the information we provide on our cards.

Target Market(s)

broad client base from church leaders to high school teachers and architects.

Industry/Entity Type

Business

Contact Information for Business Card

We format our phone number with periods not parenthesis or dashes. Information will be edited for each of our team members, and team member specific cards are not part of this scope, but rather a template so to speak.

Font styles to use
Sans Serif

Colors
6b449b
ffffff
000000
333333
aaaaaa

Requirements
Must have
• Wordmark and logo mark present (does not need to exist on the same side of card)
• Brand Colors,
• Name, Phone, Email, Address.
• Unique choices that make someone stop and take a second look
Nice to have
• It would be nice to somehow convey what we DO, as our brand name does not lend itself to this, outside of an obvious tagline though.....
• social media if not crowded. all of our handles match (instagram, twitter, facebook)
Should not have
• "clipart"

```html
<!DOCTYPE html>
<html lang="en">
<head>
<meta charset="UTF-8">
<title>Halden Business Card</title>
<link rel="stylesheet" href="https://fonts.googleapis.com/css2?family=Open+Sans:wght@400;600;700&display=swap">
<style>
  :root {
    --stage-black: #000000;
    --card-purple: #39226a;
    --ink-cream: #f3ebe6;
  }
  * { margin: 0; padding: 0; box-sizing: border-box; }
  html, body {
    width: 1200px;
    height: 899px;
    overflow: hidden;
    background: var(--stage-black);
    font-family: "Open Sans", sans-serif;
    color: var(--ink-cream);
  }
  .canvas { position: relative; width: 1200px; height: 899px; }
  .card {
    position: absolute;
    top: 274px;
    height: 294px;
    background: var(--card-purple);
  }
  .card-front {
    left: 117px;
    width: 475px;
    border-radius: 0 68px 0 68px;
  }
  .card-back {
    left: 622px;
    width: 477px;
    border-radius: 68px 0 68px 0;
  }
  .holder-name {
    position: absolute;
    left: 23px;
    top: 33px;
    font-size: 18px;
    font-weight: 600;
    letter-spacing: 0.01em;
  }
  .holder-title {
    position: absolute;
    left: 23px;
    top: 57px;
    font-size: 13.5px;
    font-weight: 400;
  }
  .wordmark {
    font-weight: 600;
    letter-spacing: 0.42em;
    line-height: 1;
    white-space: nowrap;
  }
  .card-front .wordmark {
    position: absolute;
    left: 22px;
    top: 102px;
    font-size: 32px;
  }
  .contact-list {
    position: absolute;
    right: 28px;
    top: 182px;
    list-style: none;
    text-align: right;
    font-size: 13.5px;
    line-height: 20px;
  }
  .contact-list li { display: flex; justify-content: flex-end; align-items: center; gap: 5px; }
  .contact-list svg { width: 10px; height: 10px; fill: var(--ink-cream); }
  .contact-list .address { margin-top: 4px; }
  .brand-dot {
    position: absolute;
    left: 50%;
    top: 44px;
    width: 88px;
    height: 88px;
    margin-left: -44px;
    border-radius: 50%;
    background: var(--ink-cream);
  }
  .card-back .wordmark {
    position: absolute;
    left: 0;
    right: 0;
    top: 187px;
    text-align: center;
    font-size: 28px;
    padding-left: 0.42em;
  }
  .tagline {
    position: absolute;
    left: 0;
    right: 0;
    top: 229px;
    text-align: center;
    font-size: 12.8px;
    font-weight: 700;
    line-height: 17px;
    text-transform: uppercase;
  }
</style>
</head>
<body>
<main class="canvas">
  <section class="card card-front">
    <p class="holder-name">Marcus Reed</p>
    <p class="holder-title">Managing Director</p>
    <p class="wordmark">HALDEN</p>
    <ul class="contact-list">
      <li>(044)-456-7890
        <svg viewBox="0 0 10 10" aria-hidden="true"><path d="M2 0.5 L3.6 2.6 L2.7 3.6 C3.3 5 5 6.7 6.4 7.3 L7.4 6.4 L9.5 8 L8.5 9.5 C4.5 9.3 0.7 5.5 0.5 1.5 Z"/></svg>
      </li>
      <li>info@youremail.com
        <svg viewBox="0 0 10 10" aria-hidden="true"><path d="M0.5 2 H9.5 V8 H0.5 Z M1 2.4 L5 5.4 L9 2.4" fill="none" stroke="#f3ebe6" stroke-width="1"/><path d="M0.5 2 H9.5 L5 5.3 Z"/></svg>
      </li>
      <li>www.website.com
        <svg viewBox="0 0 10 10" aria-hidden="true"><circle cx="5" cy="5" r="4.5"/><path d="M5 0.5 V9.5 M0.5 5 H9.5 M5 0.5 C2.5 3 2.5 7 5 9.5 M5 0.5 C7.5 3 7.5 7 5 9.5" fill="none" stroke="#39226a" stroke-width="0.7"/></svg>
      </li>
      <li class="address">12345, Address Goes Here Country Name, 123456</li>
    </ul>
  </section>

  <section class="card card-back">
    <span class="brand-dot" aria-hidden="true"></span>
    <p class="wordmark">HALDEN</p>
    <p class="tagline">Design and consultation company for stage and<br>TV with an emphasis in theatrical lighting.</p>
  </section>
</main>
</body>
</html>
```